Frostvale Harborline LLC

we need a business card design

Industry/Entity Type

hvac

Contact Information for Business Card

my logo

Requirements
Must have
• my logo and same colors

```html
<!DOCTYPE html>
<html lang="en">
<head>
<meta charset="utf-8">
<title>Frostvale Harborline LLC — Business Card</title>
<link rel="stylesheet" href="https://fonts.googleapis.com/css2?family=Poppins:wght@400;700&display=swap">
<style>
  :root {
    --stage: #e9ebee;
    --card: #ffffff;
    --brand-blue: #1a5ea9;
    --ink: #2b2b2b;
    --shadow: rgba(20, 30, 50, 0.18);
  }
  * { box-sizing: border-box; margin: 0; padding: 0; }
  html, body {
    width: 1200px; height: 874px; overflow: hidden;
    background: var(--stage);
    font-family: "Poppins", sans-serif;
  }
  .stage {
    width: 1200px; height: 874px;
    display: flex; align-items: center; justify-content: center; gap: 36px;
  }
  .card {
    position: relative;
    width: 546px; height: 312px;
    background: var(--card);
    border-radius: 18px;
    box-shadow: 0 10px 28px var(--shadow);
    overflow: hidden;
  }
  .brand-mark {
    display: flex; align-items: center; gap: 12px;
    color: var(--brand-blue);
    font-weight: 700;
    line-height: 1.05;
  }
  .brand-mark .dot {
    flex: none; border-radius: 50%; background: var(--brand-blue);
  }
  .card--front .brand-mark {
    position: absolute; left: 50%; top: 50%;
    transform: translate(-50%, -50%);
    font-size: 34px;
  }
  .card--front .brand-mark .dot { width: 46px; height: 46px; }

  .card--back .brand-mark {
    position: absolute; left: 34px; top: 40px;
    font-size: 24px;
  }
  .card--back .brand-mark .dot { width: 34px; height: 34px; }

  .person {
    position: absolute; right: 34px; top: 52px; text-align: right;
  }
  .person__name {
    color: var(--brand-blue); font-weight: 700; font-size: 25px; letter-spacing: 0.5px;
  }
  .person__role { color: var(--ink); font-size: 15px; margin-top: 2px; }
  .accent-bar {
    position: absolute; right: 0; top: 66px;
    width: 12px; height: 56px; background: var(--brand-blue);
  }
  .contacts {
    position: absolute; left: 34px; bottom: 38px;
    list-style: none; color: var(--ink); font-size: 14.5px;
  }
  .contacts li { display: flex; align-items: center; gap: 9px; line-height: 1.55; }
  .contacts svg { width: 14px; height: 14px; fill: var(--brand-blue); flex: none; }
  .office {
    position: absolute; right: 34px; bottom: 38px; text-align: right;
    color: var(--ink); font-size: 14.5px; line-height: 1.45;
  }
  .office__company { font-weight: 700; font-size: 15.5px; }
</style>
</head>
<body>
<main class="stage">
  <section class="card card--front" aria-label="Card front">
    <div class="brand-mark"><span class="dot"></span><span>Frostvale<br>Harborline LLC</span></div>
  </section>

  <section class="card card--back" aria-label="Card back">
    <div class="brand-mark"><span class="dot"></span><span>Frostvale<br>Harborline LLC</span></div>

    <div class="person">
      <div class="person__name">MARCUS DELANE</div>
      <div class="person__role">Managing Director</div>
    </div>
    <div class="accent-bar"></div>

    <ul class="contacts">
      <li>
        <svg viewBox="0 0 24 24" aria-hidden="true"><path d="M6.6 10.8a15.1 15.1 0 0 0 6.6 6.6l2.2-2.2a1 1 0 0 1 1-.25 11.4 11.4 0 0 0 3.6.57 1 1 0 0 1 1 1V20a1 1 0 0 1-1 1A17 17 0 0 1 3 4a1 1 0 0 1 1-1h3.5a1 1 0 0 1 1 1c0 1.25.2 2.45.57 3.6a1 1 0 0 1-.25 1z"/></svg>
        +1 555-014-2290
      </li>
      <li>
        <svg viewBox="0 0 24 24" aria-hidden="true"><path d="M2 5h20v14H2z M2 5l10 8 10-8" stroke="#fff" stroke-width="1.6"/></svg>
        hello@northwindairco.com
      </li>
      <li>
        <svg viewBox="0 0 24 24" aria-hidden="true"><circle cx="12" cy="12" r="10"/><path d="M2 12h20M12 2c3 3 3 17 0 20M12 2c-3 3-3 17 0 20" stroke="#fff" stroke-width="1.4" fill="none"/></svg>
        www.frostvaleharborline.com
      </li>
    </ul>

    <div class="office">
      <div class="office__company">Frostvale Harborline</div>
      <div>Larkport, FL, USA</div>
    </div>
  </section>
</main>
</body>
</html>
```